Velmor Spire Nine Flash website

we need a website to cater to 2 aspect of the business. We have Velmor spire residence and velmor spire office. For the office, we will get their inquire and arrange a face to face meetup to show them the office area for rent. For the residence side, it will need to be like staylane or roomvio.com. we want to allow them to book online for the date they need. We have a total of 10 different room configurations starting at $70 per night and up depending on the size of the room. example of the design is https://brisquelodge.com/

Target Market(s)

the website should have detail information on the layout, designs, and luxury of the building.

Industry/Entity Type

office and service appartment rental/lease

Coding

Coded - Design and coding required

Number of Pages Required

5+ page

Requirements
Must have
• a luxury perspective
Nice to have
• example https://brisquelodge.com/

```html
<!DOCTYPE html>
<html lang="en">
<head>
<meta charset="utf-8">
<title>Velmor Spire Nine — Meeting &amp; Staycation Haven</title>
<link href="https://fonts.googleapis.com/css2?family=Montserrat:wght@400;500;600;700;800&family=League+Spartan:wght@500;600;700&display=swap" rel="stylesheet">
<style>
:root{
  --ink:#141414;
  --charcoal:#3d3d3d;
  --charcoal-deep:#353535;
  --gold:#e3a325;
  --gold-deep:#c98d17;
  --paper:#f3f3f3;
  --white:#ffffff;
  --muted:#8a8a8a;
}
*{box-sizing:border-box;margin:0;padding:0}
html,body{width:1200px;height:4724px;overflow:hidden}
body{position:relative;background:var(--paper);font-family:"Montserrat",sans-serif;color:var(--ink)}
.abs{position:absolute}
.display{font-family:"League Spartan","Montserrat",sans-serif;font-weight:700}

/* top bar + nav */
.topbar{left:0;top:0;width:1200px;height:29px;background:var(--ink);color:var(--gold);font-size:12px;font-weight:500}
.topbar .mail{left:46px;top:7px;display:flex;gap:8px;align-items:center}
.topbar .phone{right:44px;top:7px;display:flex;gap:8px;align-items:center}
.nav{left:0;top:29px;width:1200px;height:67px;background:var(--charcoal);border-bottom:1px solid #6a5a35}
.nav-links{left:100px;top:25px;display:flex;gap:62px;color:var(--white);font-size:13px;font-weight:600;letter-spacing:.5px}
.brand-tab{left:528px;top:0;width:144px;height:96px;background:var(--ink);clip-path:polygon(0 0,100% 0,100% 100%,0 100%)}
.brand{left:528px;top:30px;width:144px;text-align:center;color:var(--gold);font-size:14px;font-weight:500;letter-spacing:.5px}
.brand .mark{display:block;width:26px;height:26px;border:1.5px solid var(--gold);margin:0 auto 6px}
.btn-line,.btn-solid{height:38px;border-radius:19px;font-size:11px;font-weight:700;display:flex;align-items:center;justify-content:center;letter-spacing:.5px}
.btn-line{left:767px;top:44px;width:160px;border:1.5px solid var(--gold);color:var(--gold)}
.btn-solid{left:936px;top:44px;width:162px;background:var(--gold);color:var(--ink)}

/* hero */
.hero{left:0;top:96px;width:1200px;height:416px;background:var(--charcoal)}
.hero-title{left:86px;top:154px;width:560px;color:var(--gold);font-size:58px;line-height:70px}
.hero-copy{left:657px;top:157px;width:450px;color:var(--white);font-size:16.5px;line-height:20px;font-weight:500}
.pill{display:flex;align-items:center;justify-content:space-between;border-radius:18px;padding:0 6px 0 16px;font-size:13px;font-weight:500}
.pill .dot{width:24px;height:24px;border-radius:50%;background:var(--gold);display:flex;align-items:center;justify-content:center}
.hero-cta{left:657px;top:257px;width:248px;height:34px;border:1.5px solid var(--gold);color:var(--gold)}
.slide{border-radius:10px;box-shadow:0 6px 16px rgba(0,0,0,.25)}
.slide-side{top:374px;width:290px;height:290px;background:linear-gradient(180deg,#d9e3ec 0%,#e9edf0 45%,#c98a4d 70%,#6d5a4a 100%)}
.slide-main{left:349px;top:352px;width:501px;height:336px;background:linear-gradient(180deg,#c7d6e4 0%,#e7ecef 35%,#e7a043 62%,#c0573c 82%,#5b7c6a 100%);border-radius:6px;z-index:2}
.play{left:572px;top:494px;width:56px;height:56px;border-radius:50%;background:rgba(255,255,255,.92);z-index:3;display:flex;align-items:center;justify-content:center}

/* section titles */
.sec-title{left:0;width:1200px;text-align:center;font-size:55px;color:#333}
.sec-title span{display:inline-block;padding:0 6px 10px;border-bottom:2px solid #9a9a9a;position:relative}
.sec-title span::after{content:"";position:absolute;left:50%;bottom:-3px;width:84px;height:4px;margin-left:-42px;background:var(--gold);border-radius:2px}
.on-dark span{color:var(--white)}

/* features */
.feature{left:50px;width:500px}
.feature .icon{width:64px;height:64px;border-radius:6px;background:var(--charcoal);display:flex;align-items:center;justify-content:center}
.feature h3{margin-top:18px;font-size:23px;font-weight:600;letter-spacing:-.3px}
.feature p{margin-top:10px;font-size:10.5px;line-height:13px;text-align:justify;font-weight:500}
.sketch{left:615px;top:877px;width:585px;height:545px;background:radial-gradient(ellipse at 70% 45%,#bdbdbd 0%,#dcdcdc 40%,var(--paper) 75%)}

/* meeting */
.photo{border-radius:4px}
.meet-a{left:92px;top:1615px;width:499px;height:334px;background:linear-gradient(180deg,#6b4a33 0%,#3a2a22 45%,#1f1a18 100%)}
.meet-b{left:607px;top:1615px;width:500px;height:334px;background:linear-gradient(180deg,#d4cfc8 0%,#b9a894 40%,#5b4034 75%,#3e2f2a 100%)}
.meet-c{left:92px;top:1963px;width:499px;height:334px;background:linear-gradient(180deg,#b9d4d4 0%,#9fc0c2 35%,#6f9597 65%,#4b5654 100%)}
.meet-card{left:607px;top:1963px;width:500px;height:334px;background:var(--white);border-radius:4px}
.meet-card h3{position:absolute;left:22px;top:20px;padding-left:10px;border-left:3px solid var(--gold);font-size:40px;line-height:48px;font-weight:600;color:#333;font-family:"League Spartan",sans-serif}
.meet-card p{position:absolute;left:22px;top:136px;width:456px;font-size:14px;line-height:18px;text-align:justify;font-weight:500}
.meet-cta{left:22px;top:268px;width:456px;height:34px;background:var(--charcoal);color:var(--gold)}

/* staycation */
.stay-head{left:70px;top:2522px;padding-left:10px;border-left:3px solid var(--gold);font-size:37px;line-height:50px;font-weight:600;color:#333;font-family:"League Spartan",sans-serif}
.stay-copy{left:668px;top:2527px;width:460px;font-size:16px;line-height:20px;font-weight:500}
.stay-card{top:2679px;width:332px;height:411px}
.stay-card .pic{position:absolute;left:0;top:0;width:332px;height:332px;border-radius:4px}
.stay-card .box{position:absolute;left:19px;top:242px;width:293px;height:169px;background:var(--gold);border-radius:3px;padding:18px 18px 0}
.stay-card h4{font-size:25px;font-weight:600;color:#222;font-family:"League Spartan",sans-serif}
.stay-card p{margin-top:10px;font-size:12px;line-height:15px;color:#2a2a2a;font-weight:500;height:32px}
.stay-card .pill{margin-top:14px;height:28px;background:var(--charcoal);color:var(--gold);font-size:9.5px}
.stay-card .pill .dot{width:20px;height:20px}

/* rooms */
.rooms{left:0;top:3143px;width:1200px;height:610px;background:var(--charcoal)}
.room{top:3308px;width:334px;height:334px;background:var(--white);border-radius:4px;overflow:hidden}
.room .pic{height:221px}
.room h5{margin:14px 0 0 9px;font-size:16px;font-weight:700}
.room .specs{margin:8px 0 0 9px;display:flex;gap:12px;align-items:center;font-size:10px;font-weight:600}
.room .specs span{display:flex;align-items:center;gap:5px}
.room .code{margin:8px 0 0 9px;font-size:10px;color:#444}
.room .price{position:absolute;right:9px;bottom:9px;color:var(--gold-deep);font-size:16px;font-weight:700}
.arrow{top:3454px;width:40px;height:40px;border:1.5px solid #bdbdbd;border-radius:50%;display:flex;align-items:center;justify-content:center}
.dots{left:509px;top:3697px;display:flex;gap:8px}
.dots i{display:block;width:40px;height:5px;border-radius:3px;background:var(--white)}
.dots i:first-child{background:var(--gold)}

/* reserve */
.reserve{left:0;top:3753px;width:1200px;height:581px;background:linear-gradient(180deg,#a8604f 0%,#c26a4e 30%,#a24b3c 55%,#6a2c2a 80%,#3d1e22 100%)}
.reserve-title{left:150px;top:3885px;width:900px;text-align:center;font-size:40px;line-height:50px;color:#4a2a25}
.reserve-title b{color:var(--gold);font-weight:700}
.reserve-copy{left:100px;top:4017px;width:1000px;text-align:center;color:var(--white);font-size:20px;line-height:27px;font-weight:500}
.field{left:336px;top:4179px;width:413px;height:38px;background:var(--white);border-radius:19px;padding-left:24px;display:flex;align-items:center;font-size:14px;font-weight:500;color:#333}
.send{left:758px;top:4179px;width:104px;height:38px;background:var(--gold);border-radius:19px;color:var(--white);display:flex;align-items:center;justify-content:center;font-size:14px;font-weight:600}

/* footer */
.footer{left:0;top:4334px;width:1200px;height:390px;background:var(--charcoal)}
.foot-brand{left:33px;top:4480px;color:var(--gold);font-size:29px;font-weight:500;letter-spacing:1px}
.foot-brand .mark{display:block;width:70px;height:70px;border:2px solid var(--gold);margin:0 0 22px 95px}
.foot-info{left:33px;top:4560px;color:var(--white);font-size:10px;line-height:13px}
.foot-info .row{display:flex;gap:8px;align-items:flex-start;margin-top:9px}
.news{left:391px;top:4380px;width:499px;height:230px;background:var(--gold);border-radius:8px;padding:22px 33px}
.news h6{font-size:14.5px;line-height:20px;font-weight:800;color:var(--white);letter-spacing:.5px}
.news .line{position:absolute;border-bottom:1.5px solid rgba(255,255,255,.85);color:rgba(255,255,255,.9);font-size:10px;padding-bottom:4px}
.news .go{position:absolute;left:33px;top:190px;width:433px;height:22px;border:1.5px solid var(--white);border-radius:11px;color:var(--white);font-size:9px;display:flex;align-items:center;justify-content:center}
.foot-menu{left:958px;top:4420px;color:var(--white);font-size:16px;line-height:32px;font-weight:500}
.foot-menu b{display:block;font-weight:700;font-size:16px}
.foot-rule{left:30px;top:4661px;width:1140px;height:2px;background:var(--gold)}
.legal{left:30px;top:4688px;color:var(--white);font-size:12.5px;display:flex;gap:22px}
.legal u{text-underline-offset:2px}
.social{right:30px;top:4685px;display:flex;gap:14px}
.social i{display:block;width:22px;height:22px;border-radius:4px;background:var(--gold)}
</style>
</head>
<body>

<!-- top bar -->
<div class="abs topbar">
  <div class="abs mail">
    <svg width="14" height="11" viewBox="0 0 14 11"><rect x="0.5" y="0.5" width="13" height="10" rx="1" fill="var(--gold)"/><path d="M1 1l6 5 6-5" stroke="#141414" fill="none"/></svg>
    info@velmorspire.nine
  </div>
  <div class="abs phone">
    <svg width="14" height="14" viewBox="0 0 14 14"><circle cx="7" cy="7" r="6.3" fill="none" stroke="var(--gold)"/><path d="M4.5 4l1.5-.5 1 2-1 .8c.4 1 1 1.6 2 2l.8-1 2 1-.5 1.5c-3 0-5.8-2.8-5.8-5.8z" fill="var(--gold)"/></svg>
    +000 000 000
  </div>
</div>

<!-- navigation -->
<div class="abs nav">
  <div class="abs nav-links"><span>DESIGN</span><span>LOCATION</span><span>EXPERIENCE</span></div>
  <div class="abs btn-line">ABOUT US</div>
  <div class="abs btn-solid">REGISTER NOW</div>
</div>
<div class="abs brand-tab" style="top:0;height:96px;clip-path:polygon(10% 0,90% 0,100% 30%,100% 100%,0 100%,0 30%)"></div>
<div class="abs brand" style="top:12px"><span class="mark"></span>Velmor Spire Nine</div>

<!-- hero -->
<div class="abs hero"></div>
<h1 class="abs hero-title display">Velmor Spire: Meeting &amp; Staycation Haven</h1>
<p class="abs hero-copy">Experience Luxury And Comfort At Velmor Spire, Our Premier Destination For Business Meetings And Staycations. Embark On Your Extraordinary Journey With Us Today!</p>
<div class="abs pill hero-cta">Learn More <span class="dot"><svg width="12" height="12" viewBox="0 0 12 12"><path d="M2 6h8M6.5 2.5L10 6l-3.5 3.5" stroke="#3d3d3d" stroke-width="1.8" fill="none"/></svg></span></div>

<div class="abs slide slide-side" style="left:77px" role="img" aria-label="Tower facade under a pale sky"></div>
<div class="abs slide slide-side" style="left:830px" role="img" aria-label="Tower facade under a pale sky"></div>
<div class="abs slide-main" role="img" aria-label="Video still: colourful tower blocks seen from below"></div>
<div class="abs play"><svg width="22" height="24" viewBox="0 0 22 24"><path d="M3 2l17 10L3 22z" fill="#3d3d3d"/></svg></div>

<!-- key features -->
<h2 class="abs sec-title display" style="top:750px"><span>Key Features</span></h2>

<div class="abs feature" style="top:881px">
  <div class="icon"><svg width="30" height="30" viewBox="0 0 30 30" fill="none" stroke="var(--gold)" stroke-width="2"><rect x="4" y="6" width="22" height="20" rx="2"/><path d="M4 12h22M10 3v6M20 3v6"/><path d="M9 17h3M14 17h3M19 17h3M9 21h3M14 21h3"/></svg></div>
  <h3>Seamless Staylane Experience</h3>
  <p>Velmor Spire Nine Offers A Seamless Staylane Experience For Both Meeting Spaces And Staycation Accommodations. With Our User-Friendly Interface, Guests Can Easily Browse Available Dates, Select Their Preferred Room Or Meeting Area, And Complete Their Staylane In Just A Few Clicks.</p>
</div>
<div class="abs feature" style="top:1068px">
  <div class="icon"><svg width="30" height="30" viewBox="0 0 30 30" fill="none" stroke="var(--gold)" stroke-width="2"><rect x="7" y="5" width="16" height="21" rx="1"/><path d="M11 10h2M17 10h2M11 15h2M17 15h2M13 26v-5h4v5M3 26h24"/></svg></div>
  <h3>Versatile Meeting Spaces</h3>
  <p>Our State-Of-The-Art Facilities Cater To A Wide Range Of Business Needs, Providing Versatile Meeting Spaces Suitable For Conferences, Seminars, Workshops, And More. Equipped With Modern Amenities And Customizable Layouts, Each Venue Offers A Conducive Environment For Productive Discussions And Collaborative Sessions.</p>
</div>
<div class="abs feature" style="top:1255px">
  <div class="icon"><svg width="30" height="30" viewBox="0 0 30 30" fill="none" stroke="var(--gold)" stroke-width="2"><path d="M4 14L15 5l11 9"/><path d="M7 12v14h16V12"/><rect x="12" y="17" width="6" height="9"/></svg></div>
  <h3>Luxurious Staycation Options</h3>
  <p>Experience Unparalleled Comfort And Luxury With Our Array Of Staycation Options At Velmor Spire Nine. Featuring Meticulously Designed Rooms And Suites, Each Accommodation Exudes Sophistication And Elegance, Providing Guests With A Tranquil Retreat Amidst The Bustling Cityscape.</p>
</div>
<div class="abs sketch" role="img" aria-label="Architectural wireframe sketch of the tower"></div>

<!-- meeting room -->
<h2 class="abs sec-title display" style="top:1492px"><span>Meeting Room</span></h2>
<div class="abs photo meet-a" role="img" aria-label="Wood-panelled boardroom with long table"></div>
<div class="abs photo meet-b" role="img" aria-label="Bright meeting room with leather chairs"></div>
<div class="abs photo meet-c" role="img" aria-label="Round conference table in a glass-walled room"></div>
<div class="abs meet-card">
  <h3>Premier Meeting Spaces<br>At Velmor Spire Nine</h3>
  <p>Elevate Your Business Gatherings At Velmor Spire Nine. Our Versatile Meeting Spaces Cater To Various Events, Equipped With Modern Amenities And Customizable Layouts For Productive Discussions. With Our Commitment To Excellence, Your Next Meeting Is Guaranteed Success.</p>
  <div class="abs pill meet-cta">Contact Us For Rental <span class="dot"><svg width="12" height="12" viewBox="0 0 12 12"><path d="M2 6h8M6.5 2.5L10 6l-3.5 3.5" stroke="#3d3d3d" stroke-width="1.8" fill="none"/></svg></span></div>
</div>

<!-- staycation -->
<h2 class="abs sec-title display" style="top:2380px"><span>Staycation</span></h2>
<h3 class="abs stay-head">Luxurious Staycation<br>Experience At Velmor Spire Nine</h3>
<p class="abs stay-copy">Indulge In Luxury At Velmor Spire Nine. Relax In Elegantly Designed Rooms, Enjoy Premium Amenities, Personalized Service, And Stunning Views For An Unforgettable Staycation.</p>

<div class="abs stay-card" style="left:64px">
  <div class="pic" role="img" aria-label="Marble bathroom with mirror and vanity" style="background:linear-gradient(180deg,#9b9b9b,#4a4a4a 60%,#2c2c2c)"></div>
  <div class="box"><h4>Bathroom Space</h4><p>Comfortable And Neatly Arranged Bathroom Decoration</p>
  <div class="pill">More About This <span class="dot"><svg width="10" height="10" viewBox="0 0 12 12"><path d="M2 6h8M6.5 2.5L10 6l-3.5 3.5" stroke="#3d3d3d" stroke-width="1.8" fill="none"/></svg></span></div></div>
</div>
<div class="abs stay-card" style="left:433px">
  <div class="pic" role="img" aria-label="Dark modern living room with sofa" style="background:linear-gradient(180deg,#5a4a3c,#3a302a 55%,#1c1a19)"></div>
  <div class="box"><h4>Livingroom Space</h4><p>Livenup At Asmorphere Of The House With Interior Design</p>
  <div class="pill">More About This <span class="dot"><svg width="10" height="10" viewBox="0 0 12 12"><path d="M2 6h8M6.5 2.5L10 6l-3.5 3.5" stroke="#3d3d3d" stroke-width="1.8" fill="none"/></svg></span></div></div>
</div>
<div class="abs stay-card" style="left:802px">
  <div class="pic" role="img" aria-label="Kitchen with shelving and wood cabinets" style="background:linear-gradient(180deg,#d8d8d8,#7c7066 50%,#3b332d)"></div>
  <div class="box"><h4>Kitchen Space</h4><p>Cooking Is Much More Convenient If Everything Neatly</p>
  <div class="pill">More About This <span class="dot"><svg width="10" height="10" viewBox="0 0 12 12"><path d="M2 6h8M6.5 2.5L10 6l-3.5 3.5" stroke="#3d3d3d" stroke-width="1.8" fill="none"/></svg></span></div></div>
</div>

<!-- room configuration -->
<div class="abs rooms"></div>
<h2 class="abs sec-title display on-dark" style="top:3190px"><span>Room Configuration</span></h2>

<div class="abs arrow" style="left:17px"><svg width="10" height="14" viewBox="0 0 10 14"><path d="M7 2L2 7l5 5" stroke="#ddd" stroke-width="1.6" fill="none"/></svg></div>
<div class="abs arrow" style="left:1141px"><svg width="10" height="14" viewBox="0 0 10 14"><path d="M3 2l5 5-5 5" stroke="#ddd" stroke-width="1.6" fill="none"/></svg></div>

<div class="abs room" style="left:79px">
  <div class="pic" role="img" aria-label="White studio with sofa and floor lamps" style="background:linear-gradient(180deg,#f2f2f2,#d9d9d9 70%,#c3c3c3)"></div>
  <h5>Type A, Studio</h5>
  <div class="specs">
    <span><svg width="16" height="12" viewBox="0 0 16 12" fill="none" stroke="#555"><rect x="1" y="4" width="14" height="5"/><rect x="3" y="1" width="4" height="3"/><path d="M1 9v2M15 9v2"/></svg>1</span>
    <span><svg width="16" height="12" viewBox="0 0 16 12" fill="none" stroke="#555"><path d="M1 6h14v2a3 3 0 01-3 3H4a3 3 0 01-3-3zM3 6V2h2"/></svg>1</span>
    <span><svg width="14" height="14" viewBox="0 0 14 14" fill="none" stroke="#555"><path d="M1 13V1h12M1 5h8v8"/></svg>36.80 m²</span>
  </div>
  <div class="code">F1202</div>
  <div class="price">$70/mo</div>
</div>
<div class="abs room" style="left:431px">
  <div class="pic" role="img" aria-label="Grey studio with shelving and lounge chair" style="background:linear-gradient(180deg,#cfcfcf,#b8b8b8 60%,#a59f97)"></div>
  <h5>Type B, Studio</h5>
  <div class="specs">
    <span><svg width="16" height="12" viewBox="0 0 16 12" fill="none" stroke="#555"><rect x="1" y="4" width="14" height="5"/><rect x="3" y="1" width="4" height="3"/><path d="M1 9v2M15 9v2"/></svg>1</span>
    <span><svg width="16" height="12" viewBox="0 0 16 12" fill="none" stroke="#555"><path d="M1 6h14v2a3 3 0 01-3 3H4a3 3 0 01-3-3zM3 6V2h2"/></svg>1</span>
    <span><svg width="14" height="14" viewBox="0 0 14 14" fill="none" stroke="#555"><path d="M1 13V1h12M1 5h8v8"/></svg>38.75 m²</span>
  </div>
  <div class="code">F1203</div>
  <div class="price">$70/mo</div>
</div>
<div class="abs room" style="left:785px">
  <div class="pic" role="img" aria-label="Warm living room with leather sofa" style="background:linear-gradient(180deg,#e7dccb,#c48a56 55%,#7a4a2c)"></div>
  <h5>Type C, One Bedroom</h5>
  <div class="specs">
    <span><svg width="16" height="12" viewBox="0 0 16 12" fill="none" stroke="#555"><rect x="1" y="4" width="14" height="5"/><rect x="3" y="1" width="4" height="3"/><path d="M1 9v2M15 9v2"/></svg>1</span>
    <span><svg width="16" height="12" viewBox="0 0 16 12" fill="none" stroke="#555"><path d="M1 6h14v2a3 3 0 01-3 3H4a3 3 0 01-3-3zM3 6V2h2"/></svg>1</span>
    <span><svg width="14" height="14" viewBox="0 0 14 14" fill="none" stroke="#555"><path d="M1 13V1h12M1 5h8v8"/></svg>47.00 m²</span>
  </div>
  <div class="code">F1201</div>
  <div class="price">$70/mo</div>
</div>
<div class="abs dots"><i></i><i></i><i></i><i></i></div>

<!-- reserve -->
<div class="abs reserve" role="img" aria-label="Sunset over a poolside terrace with palm trees and loungers"></div>
<h2 class="abs reserve-title display"><b>Reserve Your</b> Exclusive Experience at Velmor Spire Nine</h2>
<p class="abs reserve-copy">Elevate Your Next Event With Velmor Spire Nine's Premier Event Spaces. From Corporate Meetings To Lavish Celebrations, Our State-Of-The-Art Facilities And Personalized Service Ensure An Unforgettable Experience. Book Now To Indulge In Luxury And Sophistication, And Make Your Occasion Truly Remarkable.</p>
<div class="abs field">Type Your Email Address</div>
<div class="abs send">Submit</div>

<!-- footer -->
<div class="abs footer"></div>
<div class="abs foot-brand" style="top:4380px"><span class="mark"></span>VELMOR SPIRE NINE</div>
<div class="abs foot-info">
  <div style="font-size:10.5px">Contact Information</div>
  <div class="row"><svg width="12" height="14" viewBox="0 0 12 14" fill="none" stroke="#fff"><path d="M6 13s5-4.5 5-8A5 5 0 001 5c0 3.5 5 8 5 8z"/><circle cx="6" cy="5" r="1.8"/></svg><span>Orvalen Quay Road, Lantern Isle,<br>Marrowgate City</span></div>
  <div class="row"><svg width="12" height="12" viewBox="0 0 12 12" fill="none" stroke="#fff"><path d="M2 1l2.5-.2 1 2.7-1.3 1c.6 1.4 1.5 2.3 2.9 2.9l1-1.3 2.7 1L10.6 10C6 10 1.9 6 2 1z"/></svg><span>+000 000 000</span></div>
  <div class="row"><svg width="13" height="10" viewBox="0 0 13 10" fill="none" stroke="#fff"><rect x=".5" y=".5" width="12" height="9"/><path d="M1 1l5.5 4.5L12 1"/></svg><span>Info@VelmorSpire.Nine</span></div>
</div>

<div class="abs news">
  <h6>CONTACT US TO GET A UPDATED NEWS<br>INFORMATION</h6>
  <div class="line" style="left:33px;top:112px;width:210px">Email</div>
  <div class="line" style="left:258px;top:112px;width:208px">Phone Number</div>
  <div class="line" style="left:33px;top:150px;width:433px">Message</div>
  <div class="go">Submit</div>
</div>

<div class="abs foot-menu"><b>Menu</b>Design<br>Location<br>Experience<br>About Us</div>

<div class="abs foot-rule"></div>
<div class="abs legal"><span>© 2024 Velmor Spire Nine All Right Reserved.</span><span>Privacy Police</span><u>Term Of Service</u></div>
<div class="abs social" aria-label="Social links"><i></i><i></i><i></i><i></i></div>

</body>
</html>
```